Recruitment Site Design

We need a design for the login page, about page, and inner pages of a recruitment site for an oil and gas company. Design should be modern, sleek, professional and colors can be blue, green, white, orange or any other recommended colors.

Please also take into consideration that once the users login, they will need to access a form to fill in their information.

** UPDATE: Kindly provide a design for the inner information page consistent with the outer design. Attached is a picture of the basic structure. ***
Updates

Please provide a design for inner pages as shown in the design brief consistent with the registration page provided. 

Reason: We're extending it to get more inside pages.

Target Market(s)

Professionals looking for a career in the oil and gas industry in the Middle East.

Industry/Entity Type

Oil And Gas

Requirements
Must have
• Sleek design

```html
<!DOCTYPE html>
<html lang="en">
<head>
<meta charset="utf-8">
<title>About Us – Recruitment</title>
<link href="https://fonts.googleapis.com/css2?family=Arimo:wght@400;700&family=Tinos:wght@700&family=PT+Sans+Narrow&family=Open+Sans:ital,wght@0,400;1,400&display=swap" rel="stylesheet">
<style>
  :root{
    --header-blue:#1158a8;
    --nav-top:#45b4ec;
    --nav-bottom:#0f86cc;
    --page-bg:#ece9ea;
    --accent:#1aa0dc;
    --body-text:#5c5c5c;
    --quote-text:#666666;
    --link:#1158a8;
    --footer-blue:#1159a8;
    --footer-dark:#003a7a;
    --footer-rule:#333333;
    --white:#ffffff;
    --logo-text:#d3d8e2;
  }
  *{margin:0;padding:0;box-sizing:border-box}
  html,body{width:1200px;height:1200px;overflow:hidden}
  body{position:relative;background:var(--page-bg);font-family:"Arimo",Arial,sans-serif;color:var(--body-text)}
  .abs{position:absolute}

  .site-header{left:0;top:0;width:1200px;height:67px;background:var(--header-blue)}
  .brand{left:189px;top:10px;font-size:38px;font-weight:700;color:var(--logo-text);letter-spacing:.5px}
  .account-links{left:830px;top:19px;font-family:"Open Sans",sans-serif;font-size:12px;color:var(--white)}
  .account-links span{margin-right:6px}

  .main-nav{left:0;top:67px;width:1200px;height:39px;background:linear-gradient(var(--nav-top),var(--nav-bottom));border-top:2px solid #7fcaf2}
  .nav-home{left:203px;top:12px}
  .nav-item{top:14px;font-size:14px;font-weight:700;color:var(--white)}
  .nav-item.current{color:#0a0a0a}

  .page-title{left:183px;top:163px;font-size:30px;font-weight:700;color:var(--accent)}
  .intro{left:182px;top:215px;width:800px;font-size:14px;line-height:17.7px;text-align:justify}
  .intro p{margin-bottom:17.7px}
  .read-more{left:182px;top:387px;font-size:14.5px}
  .read-more a{color:var(--link);text-decoration:none}

  .divider{left:162px;width:835px;height:2px;background:linear-gradient(90deg,transparent,#a8a6a7 20%,#a8a6a7 80%,transparent)}

  .mission-title{left:194px;top:449px;width:186px;text-align:center;font-family:"Tinos",serif;font-weight:700;font-size:29px;line-height:30px;color:var(--accent)}
  .mission-quote{left:402px;top:460px;width:560px;font-family:"Tinos",serif;font-weight:700;font-size:22px;line-height:22px;color:var(--quote-text)}

  .section-title{left:182px;top:565px;font-size:19px;font-weight:700;color:var(--accent)}
  .portrait{width:90px;height:90px;border:1px solid #b9b9b9;background:linear-gradient(160deg,#f4f4f4,#9aa3ad 70%,#3b4350)}
  .member-role{font-size:18px;color:var(--accent)}
  .member-bio{width:556px;font-size:14px;line-height:17.7px}

  .info-title{left:191px;top:866px;font-size:18px;color:var(--accent)}
  .info-label{font-size:16px;color:var(--accent)}
  .info-lines{font-size:14px;line-height:23px}

  .footer-rule{left:0;top:1018px;width:1200px;height:6px;background:var(--footer-rule)}
  .site-footer{left:0;top:1024px;width:1200px;height:148px;background:var(--footer-blue)}
  .footer-heading{font-family:"PT Sans Narrow",sans-serif;font-size:19px;color:var(--white)}
  .footer-list{list-style:none;font-family:"Open Sans",sans-serif;font-size:11px;line-height:20.8px;color:var(--white);letter-spacing:-.2px}
  .news-item{font-family:"Open Sans",sans-serif;font-size:11px;color:var(--white);width:225px;letter-spacing:-.3px}
  .news-item .date{position:absolute;right:0;top:0}
  .news-item em{display:block;line-height:15px}
  .copyright{left:0;top:1172px;width:1200px;height:28px;background:var(--footer-dark);color:var(--white);font-family:"Open Sans",sans-serif;font-size:10px;text-align:center;line-height:28px}
</style>
</head>
<body>

<header class="site-header abs">
  <div class="brand abs">Company Logo</div>
  <div class="account-links abs"><span>My Account</span><span>Registered</span></div>
</header>

<nav class="main-nav abs">
  <svg class="nav-home abs" width="20" height="18" viewBox="0 0 20 18" aria-label="Home">
    <path d="M10 1 L19 9 L16.5 9 L16.5 17 L12 17 L12 12 L8 12 L8 17 L3.5 17 L3.5 9 L1 9 Z" fill="#ffffff"/>
  </svg>
  <span class="nav-item abs" style="left:238px">Categories</span>
  <span class="nav-item abs" style="left:332px">Get Stared</span>
  <span class="nav-item abs" style="left:426px">Brows Projects</span>
  <span class="nav-item abs" style="left:547px">Portfolios</span>
  <span class="nav-item current abs" style="left:632px">About Us</span>
</nav>

<h1 class="page-title abs">About Us</h1>
<div class="intro abs">
  <p>We need a design for the login page, about page, and inner pages of a recruitment site for an oil and gas company. Design should be modern, sleek, professional and colors can be blue, green, white, orange or any other recommended colors.</p>
  <p>Please also take into consideration that once the users login, they will need to access a form to fill in their information. We need a design for the login page, about page, and inner pages of a recruitment site for an oil and gas company. Design should be modern, sleek, professional and colors can be blue, green, white, orange or any other recommended colors.</p>
  <p>We need a design for the login page, about page, and inner pages of a recruitment site for an oil and gas company. Design should be modern, sleek, professional and colors can be blue, green, white, orange or any other recommended colors.</p>
</div>
<div class="read-more abs">Read more on our <a href="#">how it works page</a>.</div>

<div class="divider abs" style="top:427px"></div>
<div class="mission-title abs">Our Mission Statement</div>
<blockquote class="mission-quote abs">“We need a design for the login page, about page, and inner pages of a recruitment site for an oil and gas ”</blockquote>
<div class="divider abs" style="top:536px"></div>

<h2 class="section-title abs">Management Team</h2>

<div class="portrait abs" style="left:212px;top:603px" role="img" aria-label="Portrait photo of the managing director"></div>
<h3 class="member-role abs" style="left:312px;top:601px">Managing Director</h3>
<p class="member-bio abs" style="left:315px;top:629px">We need a design for the login page, about page, and inner pages of a recruitment site for an oil and gas company. Design should be modern, sleek, professional and colors can be blue, green, white, orange or any other recommended colors.</p>

<div class="portrait abs" style="left:212px;top:728px;height:88px" role="img" aria-label="Portrait photo of the assistant managing director"></div>
<h3 class="member-role abs" style="left:310px;top:726px">Assistant Managing</h3>
<p class="member-bio abs" style="left:313px;top:761px">We need a design for the login page, about page, and inner pages of a recruitment site for an oil and gas company. Design should be modern, sleek, professional and colors can be blue, green, white, orange or any other recommended colors.</p>

<div class="divider abs" style="top:851px"></div>

<h2 class="info-title abs">Company Information</h2>
<div class="info-label abs" style="left:190px;top:899px">Incorporation</div>
<div class="info-lines abs" style="left:190px;top:919px">Northwell Crest Pty Ltd<br>ABN: 48 315 902 617</div>
<div class="info-label abs" style="left:484px;top:899px">Established</div>
<div class="info-lines abs" style="left:487px;top:917px">July , 2010</div>
<div class="info-label abs" style="left:690px;top:893px;font-size:17px">Address</div>
<div class="info-lines abs" style="left:690px;top:916px">Level 6,<br>18 Harbour Lane,<br>Marlow Bay 2040<br>NSW UAE</div>

<div class="footer-rule abs"></div>
<footer class="site-footer abs">
  <div class="footer-heading abs" style="left:203px;top:10px">Support</div>
  <ul class="footer-list abs" style="left:206px;top:38px">
    <li>Client Integration</li><li>Improved Performance</li><li>Customer Support</li><li>Our Business Helpline</li>
  </ul>
  <div class="footer-heading abs" style="left:361px;top:11px">Financial Success</div>
  <ul class="footer-list abs" style="left:366px;top:38px">
    <li>Consequat Nunc Nibh</li><li>Improved Performance</li><li>Proin Cras Vault</li><li>Our Business Helpline</li><li>Voluptous</li>
  </ul>
  <div class="footer-heading abs" style="left:541px;top:8px">Business Guidelines</div>
  <ul class="footer-list abs" style="left:552px;top:44px">
    <li>Client Integration</li><li>Improved Performance</li><li>Customer Support</li><li>Our Business Helpline</li>
  </ul>
  <div class="footer-heading abs" style="left:743px;top:8px">Latest News &amp; Events</div>
  <div class="news-item abs" style="left:746px;top:47px">Cras Quam Nibh Fullem Nest<span class="date">4/21/11</span><em>Loresto mesemt maruis neterin</em></div>
  <div class="news-item abs" style="left:746px;top:91px;width:218px">Mauris Netrem<span class="date">4/11/11</span><em>Mesemt maruis neterin</em></div>
</footer>
<div class="copyright abs">©2011 All Rights Reserved</div>

</body>
</html>
```